Travel Agency Website - Simple General

Need a 7 page simple design that is pretty repetitive. Need to be able to load quickly that is SEO optimized. Trying to give ideas on what they can do, be personal as we are local, but at the same time come across as professional and get information easily with little burden.

- Landing Page
- Brimwell Vacations Page
- Family Trips
- Road Trips from Texas
- Other Destinations
- About Us Page
- Contact Us Page

Target Market(s)

Families

Coding

Coded - Design and coding required

Number of Pages Required

5+ page

Colors

Designer to choose colors to be used in the design.

Requirements
Must have
• Like it to flow easily with our logo. Use that for colors, etc.

```html
<!DOCTYPE html>
<html lang="en">
<head>
<meta charset="utf-8">
<title>Contact Page Designs – Meadowlark Travel Co.</title>
<link rel="stylesheet" href="https://fonts.googleapis.com/css2?family=Jost:wght@500;600&family=Manrope:wght@400;500;600;700;800&display=swap">
<style>
  :root {
    --board: #a2a2a2;
    --teal: #1d5f6c;
    --teal-2: #2b7480;
    --gold: #c99a4c;
    --ink: #1f5b67;
    --muted: #4f6d72;
    --line: #c9d3d1;
    --white: #ffffff;
    --sky-top: #edf2f1;
    --sky-bottom: #f3f2eb;
  }
  * { box-sizing: border-box; margin: 0; padding: 0; }
  html, body { width: 1200px; height: 637px; overflow: hidden; }
  body { background: var(--board); font-family: "Manrope", sans-serif; position: relative; }

  .board-title {
    position: absolute; left: 0; top: 38px; width: 1200px; text-align: center;
    font-family: "Jost", sans-serif; font-weight: 600; font-size: 64px; letter-spacing: 2px;
    color: var(--white); line-height: 1;
  }

  .page {
    position: absolute; top: 185px; width: 503px; height: 365px; overflow: hidden;
    background: linear-gradient(180deg, var(--sky-top) 0%, #e6eeec 45%, var(--sky-bottom) 75%);
    color: var(--ink);
  }
  .page--teal { left: 84px; }
  .page--light { left: 613px; }
  .page__scenery {
    position: absolute; left: 0; top: 50px; width: 100%; height: 180px;
    background: linear-gradient(180deg, rgba(220,231,229,0) 0%, rgba(205,220,218,0.55) 55%, rgba(243,242,235,0) 100%);
  }

  .topbar {
    position: absolute; left: 230px; top: 0; width: 234px; height: 18px;
    background: var(--teal); border-radius: 0 0 5px 5px;
    display: flex; align-items: center; justify-content: center; gap: 10px;
    color: var(--white); font-size: 5.6px; font-weight: 500;
  }
  .topbar__item { display: flex; align-items: center; gap: 4px; }
  .topbar__dot { width: 11px; height: 11px; border-radius: 50%; background: var(--white); display: flex; align-items: center; justify-content: center; }
  .topbar__dot svg { width: 7px; height: 7px; fill: var(--teal); }

  .brand {
    position: absolute; left: 30px; top: 14px; width: 92px; height: 56px;
    display: flex; flex-direction: column; align-items: center; justify-content: center; gap: 4px;
  }
  .brand__mark { width: 12px; height: 12px; border-radius: 50%; background: var(--gold); }
  .brand__name { font-size: 9px; font-weight: 700; color: var(--teal); text-align: center; line-height: 1.15; }

  .nav {
    position: absolute; left: 133px; top: 27px; height: 16px;
    display: flex; align-items: center; gap: 9.5px; font-size: 6.2px; font-weight: 500; color: var(--ink);
  }
  .nav__home { width: 6px; height: 6px; fill: var(--gold); }
  .nav__about { margin-left: 5px; }
  .nav__cta {
    display: flex; align-items: center; gap: 6px; height: 16px; padding: 0 3px 0 10px;
    background: var(--gold); color: var(--white); border-radius: 8px; font-size: 5.6px;
  }
  .nav__cta-arrow { width: 10px; height: 10px; border-radius: 50%; background: rgba(255,255,255,0.25); display: flex; align-items: center; justify-content: center; }
  .nav__cta-arrow svg { width: 5px; height: 5px; stroke: var(--white); fill: none; stroke-width: 1.6; }

  .intro { position: absolute; left: 50px; top: 98px; width: 180px; }
  .page--light .intro { top: 104px; }
  .intro__eyebrow { font-size: 9.6px; font-weight: 500; letter-spacing: 0.3px; color: var(--ink); line-height: 1.1; }
  .intro__title { font-size: 22px; font-weight: 800; color: var(--teal); line-height: 1; margin-top: 1px; position: relative; display: inline-block; }
  .sparkle { position: absolute; width: 7px; height: 7px; fill: var(--gold); }
  .intro__title .sparkle { right: -6px; top: -4px; }
  .intro__text { font-size: 6.3px; line-height: 1.75; color: var(--muted); margin-top: 11px; width: 178px; }

  .contact-item { display: flex; align-items: center; gap: 8px; margin-top: 14px; }
  .contact-item + .contact-item { margin-top: 9px; padding-top: 8px; border-top: 0.6px solid var(--line); width: 160px; }
  .contact-item__icon { width: 24px; height: 24px; border-radius: 50%; background: var(--gold); display: flex; align-items: center; justify-content: center; flex-shrink: 0; }
  .contact-item__icon svg { width: 9px; height: 9px; fill: var(--white); }
  .contact-item__label { font-size: 7px; color: var(--ink); line-height: 1.3; }
  .contact-item__value { font-size: 8px; font-weight: 500; color: var(--teal); line-height: 1.5; }

  .social { display: flex; gap: 5px; margin-top: 19px; }
  .social__dot { width: 17px; height: 17px; border-radius: 50%; background: var(--teal); }

  .enquiry {
    position: absolute; left: 252px; top: 81px; width: 212px; height: 218px; border-radius: 5px;
    padding: 20px 16px 0 20px;
  }
  .page--teal .enquiry { background: linear-gradient(160deg, var(--teal) 0%, var(--teal-2) 100%); }
  .page--light .enquiry { background: var(--white); border: 0.8px solid var(--line); }
  .enquiry__title { font-size: 9.4px; font-weight: 800; letter-spacing: 0.1px; position: relative; display: inline-block; }
  .page--teal .enquiry__title { color: var(--white); }
  .page--light .enquiry__title { color: var(--teal); }
  .enquiry__title .sparkle { right: -7px; top: -5px; }
  .field {
    display: flex; align-items: center; gap: 6px; width: 175px; height: 22px; margin-top: 6px;
    background: var(--white); padding: 0 9px; font-size: 6.2px; color: var(--ink);
  }
  .page--light .field { border: 0.7px solid var(--teal); }
  .enquiry__title + .field { margin-top: 11px; }
  .field svg { width: 5.5px; height: 5.5px; fill: #9aa9ab; flex-shrink: 0; }
  .field--area { height: 44px; align-items: flex-start; padding-top: 7px; }
  .enquiry__submit {
    display: inline-flex; align-items: center; gap: 8px; margin-top: 7px; height: 20px; padding: 0 3px 0 14px;
    border-radius: 10px; font-size: 7.2px; font-weight: 500; color: var(--white);
  }
  .page--teal .enquiry__submit { background: var(--gold); }
  .page--light .enquiry__submit { background: var(--teal); }
  .enquiry__submit .nav__cta-arrow { width: 14px; height: 14px; }
  .enquiry__submit .nav__cta-arrow svg { width: 6px; height: 6px; }

  .footer {
    position: absolute; left: 0; top: 337px; width: 100%; height: 28px; background: var(--white);
    font-size: 5.4px; color: #35494c;
  }
  .footer__copy { position: absolute; left: 0; width: 470px; top: 11px; text-align: center; }
  .footer__social { position: absolute; left: 416px; top: 9px; display: flex; gap: 3px; }
  .footer__social span { width: 9px; height: 9px; border-radius: 50%; background: var(--teal); }
</style>
</head>
<body>
<svg width="0" height="0" style="position:absolute" aria-hidden="true">
  <defs>
    <symbol id="i-mail" viewBox="0 0 24 24"><path d="M2 5h20v14H2z M3 6l9 7 9-7" /><path d="M2 5h20v2l-10 7L2 7z" fill-opacity="0.6"/></symbol>
    <symbol id="i-phone" viewBox="0 0 24 24"><path d="M6.6 10.8a15.1 15.1 0 0 0 6.6 6.6l2.2-2.2c.3-.3.7-.4 1-.2 1.1.4 2.3.6 3.6.6.6 0 1 .4 1 1V20c0 .6-.4 1-1 1A17 17 0 0 1 3 4c0-.6.4-1 1-1h3.5c.6 0 1 .4 1 1 0 1.3.2 2.5.6 3.6.1.3 0 .7-.2 1z"/></symbol>
    <symbol id="i-user" viewBox="0 0 24 24"><circle cx="12" cy="7" r="5"/><path d="M2 22c0-5.5 4.5-9 10-9s10 3.5 10 9z"/></symbol>
    <symbol id="i-lines" viewBox="0 0 24 24"><path d="M2 5h20v2H2zM2 11h20v2H2zM2 17h20v2H2z"/></symbol>
    <symbol id="i-home" viewBox="0 0 24 24"><path d="M12 2 1 12h3v10h6v-6h4v6h6V12h3z"/></symbol>
    <symbol id="i-arrow" viewBox="0 0 10 10"><path d="M2 8 8 2M3.5 2H8v4.5"/></symbol>
    <symbol id="i-spark" viewBox="0 0 10 10"><path d="M5 0 6 4 10 5 6 6 5 10 4 6 0 5 4 4z"/></symbol>
  </defs>
</svg>

<h1 class="board-title">CONTACT PAGE DESIGNS</h1>

<!-- Variant: teal enquiry panel -->
<section class="page page--teal">
  <div class="page__scenery" role="img" aria-label="Soft misty mountain landscape backdrop"></div>
  <div class="topbar">
    <span class="topbar__item"><span class="topbar__dot"><svg><use href="#i-mail"/></svg></span>hello@meadowlarktravel.com</span>
    <span class="topbar__item"><span class="topbar__dot"><svg><use href="#i-phone"/></svg></span>Phone Number (555) 014 2290</span>
  </div>
  <div class="brand"><span class="brand__mark"></span><span class="brand__name">Meadowlark<br>Travel Co.</span></div>
  <nav class="nav">
    <svg class="nav__home"><use href="#i-home"/></svg>
    <span>Brimwell Vacations</span><span>Family Trips</span><span>Texas Road Trips</span><span>Other Destinations</span>
    <span class="nav__about">About Us</span>
    <span class="nav__cta">Contact Us<span class="nav__cta-arrow"><svg><use href="#i-arrow"/></svg></span></span>
  </nav>
  <div class="intro">
    <p class="intro__eyebrow">GET IN TOUCH</p>
    <h2 class="intro__title">CONTACT US<svg class="sparkle"><use href="#i-spark"/></svg></h2>
    <p class="intro__text">Let us help you create memorable travel experiences with personalized planning designed around your needs.</p>
    <div class="contact-item"><span class="contact-item__icon"><svg><use href="#i-phone"/></svg></span><div><p class="contact-item__label">Phone number</p><p class="contact-item__value">(555) 014 2290</p></div></div>
    <div class="contact-item"><span class="contact-item__icon"><svg><use href="#i-mail"/></svg></span><div><p class="contact-item__label">Email address</p><p class="contact-item__value">hello@meadowlarktravel.com</p></div></div>
    <div class="social"><span class="social__dot"></span><span class="social__dot"></span></div>
  </div>
  <form class="enquiry">
    <h3 class="enquiry__title">START PLANNING YOUR JOURNEY<svg class="sparkle"><use href="#i-spark"/></svg></h3>
    <div class="field"><svg><use href="#i-user"/></svg>Name</div>
    <div class="field"><svg><use href="#i-mail"/></svg>Email address</div>
    <div class="field"><svg><use href="#i-phone"/></svg>Phone number</div>
    <div class="field field--area"><svg><use href="#i-lines"/></svg>Any details you want us to know?</div>
    <span class="enquiry__submit">Contact Us<span class="nav__cta-arrow"><svg><use href="#i-arrow"/></svg></span></span>
  </form>
  <footer class="footer">
    <p class="footer__copy">© 2026 Meadowlark Travel Co. All Right Reserved</p>
    <div class="footer__social"><span></span><span></span></div>
  </footer>
</section>

<!-- Variant: light enquiry panel -->
<section class="page page--light">
  <div class="page__scenery" role="img" aria-label="Soft misty mountain landscape backdrop"></div>
  <div class="topbar">
    <span class="topbar__item"><span class="topbar__dot"><svg><use href="#i-mail"/></svg></span>hello@meadowlarktravel.com</span>
    <span class="topbar__item"><span class="topbar__dot"><svg><use href="#i-phone"/></svg></span>Phone Number (555) 014 2290</span>
  </div>
  <div class="brand"><span class="brand__mark"></span><span class="brand__name">Meadowlark<br>Travel Co.</span></div>
  <nav class="nav">
    <svg class="nav__home"><use href="#i-home"/></svg>
    <span>Brimwell Vacations</span><span>Family Trips</span><span>Texas Road Trips</span><span>Other Destinations</span>
    <span class="nav__about">About Us</span>
    <span class="nav__cta">Contact Us<span class="nav__cta-arrow"><svg><use href="#i-arrow"/></svg></span></span>
  </nav>
  <div class="intro">
    <p class="intro__eyebrow">GET IN TOUCH</p>
    <h2 class="intro__title">CONTACT US<svg class="sparkle"><use href="#i-spark"/></svg></h2>
    <p class="intro__text">Let us help you create memorable travel experiences with personalized planning designed around your needs.</p>
    <div class="contact-item"><span class="contact-item__icon"><svg><use href="#i-phone"/></svg></span><div><p class="contact-item__label">Phone number</p><p class="contact-item__value">(555) 014 2290</p></div></div>
    <div class="contact-item"><span class="contact-item__icon"><svg><use href="#i-mail"/></svg></span><div><p class="contact-item__label">Email address</p><p class="contact-item__value">hello@meadowlarktravel.com</p></div></div>
    <div class="social"><span class="social__dot"></span><span class="social__dot"></span></div>
  </div>
  <form class="enquiry">
    <h3 class="enquiry__title">START PLANNING YOUR JOURNEY<svg class="sparkle"><use href="#i-spark"/></svg></h3>
    <div class="field"><svg><use href="#i-user"/></svg>Name</div>
    <div class="field"><svg><use href="#i-mail"/></svg>Email address</div>
    <div class="field"><svg><use href="#i-phone"/></svg>Phone number</div>
    <div class="field field--area"><svg><use href="#i-lines"/></svg>Any details you want us to know?</div>
    <span class="enquiry__submit">Contact Us<span class="nav__cta-arrow"><svg><use href="#i-arrow"/></svg></span></span>
  </form>
  <footer class="footer">
    <p class="footer__copy">© 2026 Meadowlark Travel Co. All Right Reserved</p>
    <div class="footer__social"><span></span><span></span></div>
  </footer>
</section>
</body>
</html>
```